Modern card design needed for building development company

We are looking for a sharp modern new look for our business cards.
We are a New Zealand based company called TKR Ventures NZ LTD that specialises in subdividing large sections, housing and commercial buildings.
We have attached a photo of the current logo and would like to see it improved somehow as it looks a bit dated.
We are open to any colours.

Target Market(s)

Investors, Property buyers

Industry/Entity Type

Investment

Contact Information for Business Card

TKR VENTURES NZ LTD
www.tkrventuresnz.co.nz

Damon Whitcombe
Phone +64 21 938 104
Email dpwhitcombe@korumail.co.nz

Font styles to use
Serif
Sans Serif

Colors
0792cd
33a6d7
85cae6
6b449b
886aae
f04a50
ec1f27
f37122
f68d4d

Requirements
Must have
• Please try and make the logo more modern or if you have a similar one we would like to see it.

```html
<!DOCTYPE html>
<html lang="en">
<head>
<meta charset="utf-8">
<title>TKR Ventures NZ LTD — Business Card</title>
<link rel="stylesheet" href="https://fonts.googleapis.com/css2?family=Work+Sans:wght@400;500;700&display=swap">
<style>
  :root {
    --stage: #1b1b1d;
    --card-black: #0b0b0c;
    --card-black-2: #151517;
    --brand-blue: #0792cd;
    --brand-blue-light: #33a6d7;
    --brand-blue-pale: #85cae6;
    --white: #ffffff;
    --text-soft: #e8e8e8;
  }
  * { margin: 0; padding: 0; box-sizing: border-box; }
  html, body {
    width: 1200px; height: 963px; overflow: hidden;
    background: var(--stage);
    font-family: "Work Sans", Arial, sans-serif;
  }
  .canvas {
    width: 1200px; height: 963px;
    display: flex; flex-direction: column;
    align-items: center; justify-content: center; gap: 56px;
  }
  .card {
    position: relative;
    width: 700px; height: 400px;
    border-radius: 18px;
    overflow: hidden;
    box-shadow: 0 18px 40px rgba(0,0,0,.45);
  }

  /* Front */
  .card-front {
    background: linear-gradient(160deg, var(--card-black-2), var(--card-black) 60%);
  }
  .front-brand {
    position: absolute; left: 60px; top: 130px; width: 210px;
    text-align: center; color: var(--brand-blue);
  }
  .brand-name {
    font-weight: 500; letter-spacing: 2px; line-height: 1.2;
  }
  .front-brand .brand-name { font-size: 22px; }
  .front-brand .brand-sub { font-size: 11px; letter-spacing: 4px; }
  .brand-sub {
    display: flex; align-items: center; justify-content: center; gap: 10px;
    margin-top: 6px; font-weight: 500;
  }
  .brand-sub::before, .brand-sub::after {
    content: ""; display: block; width: 42px; height: 1px; background: currentColor;
  }
  .front-divider {
    position: absolute; left: 300px; top: 95px;
    width: 1px; height: 170px; background: var(--brand-blue);
  }
  .contact-block {
    position: absolute; left: 335px; top: 120px; color: var(--white);
  }
  .contact-name {
    font-size: 30px; font-weight: 700; letter-spacing: .5px;
    text-transform: uppercase; margin-bottom: 22px;
  }
  .contact-line {
    display: flex; align-items: center; gap: 12px;
    font-size: 18px; color: var(--text-soft); margin-bottom: 6px;
  }
  .contact-line svg { width: 13px; height: 13px; flex: none; }
  .web-band {
    position: absolute; right: 0; bottom: 0;
    width: 390px; height: 40px;
    background: var(--brand-blue);
    clip-path: polygon(28px 0, 100% 0, 100% 100%, 0 100%);
    display: flex; align-items: center; justify-content: center;
    color: var(--white); font-size: 17px; letter-spacing: .3px;
    padding-left: 28px;
  }

  /* Back */
  .card-back {
    background: linear-gradient(135deg, var(--brand-blue-light), var(--brand-blue) 70%);
    display: flex; align-items: center; justify-content: center;
  }
  .back-brand { text-align: center; color: var(--white); }
  .back-brand .brand-name { font-size: 40px; letter-spacing: 4px; }
  .back-brand .brand-sub { font-size: 15px; letter-spacing: 6px; margin-top: 10px; }
  .back-brand .brand-sub::before, .back-brand .brand-sub::after { width: 80px; }
</style>
</head>
<body>
<main class="canvas">
  <section class="card card-front" aria-label="Business card front">
    <div class="front-brand">
      <div class="brand-name">TKR VENTURES</div>
      <div class="brand-sub">NZ LTD</div>
    </div>
    <div class="front-divider"></div>
    <div class="contact-block">
      <div class="contact-name">Damon Whitcombe</div>
      <div class="contact-line">
        <svg viewBox="0 0 24 24" aria-hidden="true"><path fill="#0792cd" d="M6.6 10.8a15 15 0 0 0 6.6 6.6l2.2-2.2a1 1 0 0 1 1-.25 11.4 11.4 0 0 0 3.6.57 1 1 0 0 1 1 1V20a1 1 0 0 1-1 1A17 17 0 0 1 3 4a1 1 0 0 1 1-1h3.5a1 1 0 0 1 1 1c0 1.25.2 2.45.57 3.6a1 1 0 0 1-.25 1z"/></svg>
        <span>+64 21 938 104</span>
      </div>
      <div class="contact-line">
        <svg viewBox="0 0 24 24" aria-hidden="true"><rect x="2" y="5" width="20" height="14" rx="2" fill="none" stroke="#0792cd" stroke-width="2"/><path d="M3 6l9 7 9-7" fill="none" stroke="#0792cd" stroke-width="2"/></svg>
        <span>dpwhitcombe@korumail.co.nz</span>
      </div>
    </div>
    <div class="web-band">www.tkrventuresnz.co.nz</div>
  </section>

  <section class="card card-back" aria-label="Business card back">
    <div class="back-brand">
      <div class="brand-name">TKR VENTURES</div>
      <div class="brand-sub">NZ LTD</div>
    </div>
  </section>
</main>
</body>
</html>
```